Small legal and financial translation company needs Squarespace website, brochure and logo

Hello,
We are Lumarin Services (www.lumarinservices-example.com), a boutique legal and financial translation company. We offer our services mainly to Spanish customers. Our primary line of business is the translation of financial statements, but we translate a wide variety legal and financial texts.
The project we are offering comprises three parts: a redo of the current website, an informational brochure for potential customer and a logo design. These three parts should provide a consistent image. We would develop content soon.
We are looking for a website that would look like a typical law firm website, nothing too fancy. Right now, it is in English, Spanish and French, although the new site need only be in English and Spanish. There must be good toggling between the English and Spanish versions. There would be no need for tie-ins to social media and it would not contain a blog. Basically, a static site. We aren't interesting in driving traffic to the site or SEO, as we will contact nearly all potential customers beforehand. The website must be built in Squarespace to enable a smooth transition. The content would be similar to the current page, we'll be working on the exact content, but a rough draft is attached.
The brochure will be some three pages and would introduce the company to potential customers, using similar images as the website and the logo to be designed.
The only specifications for the logo is, as the website and brochure, it convey a sense of security and trust.
Feel free to ask with any questions as this is the first time we have used this platform.
Thank you!
Updates

I've added a more or less final version for the text in the brochure and updated the brief. Added Wednesday, June 10, 2015

Target Market(s)

Spanish law firms, auditors, accountants, banks, investment firms

Industry/Entity Type

Finance

Logo Text

Lumarin Services

Number of Pages Required

5+ page

Font styles to use
Serif

Requirements
Must have
• The website must be built in Squarespace and have a good option to toggle between English and Spanish versions.
• Brochure must be in both English and Spanish, I'm attaching a rough draft of the information that it will probably have. This should give an idea about what to include and the spacing. I will update it to include the final information.
Nice to have
• Would be nice to have some quality finance- and legal-related images
Should not have
• Vibrant colours

```html
<!DOCTYPE html>
<html lang="en">
<head>
<meta charset="utf-8">
<title>Lumarin Services — Legal and Financial Translation</title>
<link rel="stylesheet" href="https://fonts.googleapis.com/css2?family=Cinzel:wght@400;500&family=Crimson+Text:wght@400;600&family=Open+Sans:wght@400;600&display=swap">
<style>
:root{
  --black:#000;
  --ink:#111;
  --white:#fff;
  --band:#c9c9c9;
  --text:#1e1e1e;
  --muted:#d8d8d8;
  --line:#d0d0d0;
  --accent:#e53935;
  --link:#4a8ee0;
  --serif-display:'Cinzel', serif;
  --serif:'Crimson Text', serif;
  --sans:'Open Sans', sans-serif;
}
*{box-sizing:border-box;margin:0;padding:0}
html,body{width:1200px;height:2226px;overflow:hidden}
body{position:relative;background:var(--white);font-family:var(--sans);color:var(--text)}
h2,h3,h4{font-weight:400}
.abs{position:absolute}

/* top bar */
.topbar{left:0;top:0;width:1200px;height:28px;background:var(--black);color:var(--white);font-size:10px}
.lang{position:absolute;right:80px;top:6px;display:flex;align-items:center;gap:6px}
.lang-select{border:1px solid var(--white);padding:0 14px 0 4px;height:17px;line-height:15px;position:relative}
.lang-select::after{content:"";position:absolute;right:4px;top:6px;border:3px solid transparent;border-top-color:var(--white)}

/* header */
.header{left:0;top:28px;width:1200px;height:98px;background:var(--white);border-bottom:2px solid var(--black)}
.brand{position:absolute;left:102px;top:26px;font-family:var(--serif-display);font-size:38px;letter-spacing:1px;color:var(--ink)}
.nav{position:absolute;right:98px;top:40px;display:flex;gap:38px;font-family:var(--serif);font-size:20px;color:var(--ink)}

/* hero */
.hero{left:0;top:126px;width:1200px;height:454px;background:linear-gradient(120deg,#2b2b2b 0%,#6e6e6e 35%,#bdbdbd 55%,#8a8a8a 75%,#3a3a3a 100%)}
.hero-tag{left:566px;top:278px;width:634px;height:84px;background:rgba(255,255,255,.55);display:flex;align-items:center;justify-content:center;font-size:31px;color:#111;letter-spacing:.2px}
.band{left:0;top:580px;width:1200px;height:246px;background:var(--band)}
.service{top:545px;width:305px;height:230px;background:var(--black);color:var(--white);text-align:center}
.service-icon{position:absolute;left:50%;top:-58px;margin-left:-58px;width:116px;height:116px;border-radius:50%;background:var(--black);border:4px solid var(--white);box-shadow:0 0 0 3px var(--black);display:flex;align-items:center;justify-content:center}
.service-title{margin-top:76px;font-family:var(--serif-display);font-size:20px;font-weight:400;letter-spacing:1px;white-space:nowrap}
.service-text{margin:12px auto 0;width:230px;font-size:15px;line-height:17px}
.btn{display:inline-block;border:1.5px solid var(--white);border-radius:5px;font-size:15px;width:96px;height:31px;line-height:28px;text-align:center}
.service .btn{margin-top:18px}

/* about */
.video{left:100px;top:881px;width:494px;height:310px;background:#1a1a1a}
.video-frame{position:absolute;left:0;top:0;width:494px;height:280px;background:linear-gradient(100deg,#5a5a5a 0%,#cfcfcf 30%,#3a3a3a 50%,#bbbbbb 75%,#e0e0e0 100%)}
.video-bar{position:absolute;left:0;top:280px;width:494px;height:30px;display:flex;align-items:center;gap:10px;padding:0 10px;color:var(--white);font-size:12px}
.progress{flex:1;height:3px;background:var(--accent)}
.about{left:625px;top:875px;width:475px}
.h-section{font-family:var(--serif-display);font-size:29px;font-weight:400;letter-spacing:1px}
.about p{margin-top:10px;font-size:16px;line-height:23.5px;text-align:justify}
.btn-dark{border-color:var(--ink);color:var(--ink);margin-top:14px;width:97px;height:33px;line-height:30px;border-width:2px}

/* why */
.why{left:0;top:1252px;width:1200px;height:405px;background:linear-gradient(110deg,#0c0c0c 0%,#2a2a2a 40%,#141414 55%,#3a3a3a 80%,#0e0e0e 100%);color:var(--white)}
.why .h-section{position:absolute;top:46px;width:100%;text-align:center;font-size:28px}
.reason{position:absolute;top:124px;width:320px}
.reason-icon{position:absolute;left:0;top:0;width:64px;height:64px;border-radius:50%;border:2px solid var(--white);display:flex;align-items:center;justify-content:center}
.reason h3{margin-left:76px;padding-top:14px;font-family:var(--serif);font-weight:400;font-size:21px}
.reason p{margin:6px 0 0 76px;width:217px;font-size:13.5px;line-height:22.5px;text-align:justify;hyphens:auto;color:var(--muted)}

/* clients */
.clients-h{left:0;top:1702px;width:1200px;text-align:center;font-size:28px}
.clients{left:100px;top:1784px;width:1000px;height:101px;border:1px solid var(--line);display:flex}
.client{flex:1;border-right:1px solid var(--line);display:flex;align-items:center;justify-content:center;gap:8px;font-family:var(--sans);font-weight:600;font-size:20px;color:#333}
.client:last-child{border-right:0}
.client-dot{width:22px;height:22px;border-radius:50%;background:#333}

/* footer */
.footer{left:0;top:1938px;width:1200px;height:288px;background:var(--black);color:var(--white)}
.fcol{position:absolute;top:32px}
.fcol h4{font-size:16px;font-weight:600;margin-bottom:14px}
.fcol ul{list-style:none}
.fcol li{font-size:14.5px;line-height:31.5px;padding-left:14px;position:relative}
.fcol li::before{content:"";position:absolute;left:0;top:14px;width:4px;height:4px;border-radius:50%;background:var(--white)}
.contact{width:235px}
.contact p{font-size:14px;line-height:22px;margin-bottom:9px;white-space:nowrap}
.contact a{color:var(--link);text-decoration:none}
.field{width:230px;height:26px;background:#d4d4d4;margin-bottom:6px;font-size:11px;color:#777;padding:5px 8px}
.field-msg{height:76px}
.send{margin-top:6px;display:inline-block;border:1px solid var(--white);font-size:12px;padding:5px 9px}
</style>
</head>
<body>

<div class="abs topbar">
  <div class="lang"><span>Select Language:</span><span class="lang-select">English</span></div>
</div>

<header class="abs header">
  <div class="brand">LUMARIN SERVICES</div>
  <nav class="nav"><span>Home</span><span>About Us</span><span>Services</span><span>FAQ's</span><span>Contact Us</span></nav>
</header>

<div class="abs hero" role="img" aria-label="Black and white photo of a hand signing a document beside an official stamp"></div>
<div class="abs hero-tag">HIGH-QUALITY TRANSLATION SERVICES</div>
<div class="abs band"></div>

<section class="abs service" style="left:115px">
  <div class="service-icon">
    <svg width="62" height="62" viewBox="0 0 62 62" fill="#fff"><rect x="22" y="6" width="24" height="12" rx="2" transform="rotate(35 34 12)"/><rect x="26" y="18" width="6" height="28" transform="rotate(-55 29 32)"/><rect x="12" y="48" width="30" height="6"/></svg>
  </div>
  <h2 class="service-title">Legal Translation</h2>
  <p class="service-text">Lorem ipsum dolor sit amet, consectetuer adipiscing elit, sed diam nonummy nibh.</p>
  <span class="btn">More</span>
</section>
<section class="abs service" style="left:447px">
  <div class="service-icon">
    <svg width="56" height="56" viewBox="0 0 56 56" fill="none" stroke="#fff" stroke-width="3"><rect x="8" y="6" width="40" height="42" rx="3"/><circle cx="28" cy="27" r="9"/><path d="M28 18v18M19 27h18"/><path d="M13 48v4M43 48v4"/></svg>
  </div>
  <h2 class="service-title">Financial Translation</h2>
  <p class="service-text">Lorem ipsum dolor sit amet, consectetuer adipiscing elit, sed diam nonummy nibh.</p>
  <span class="btn">More</span>
</section>
<section class="abs service" style="left:780px">
  <div class="service-icon">
    <svg width="64" height="44" viewBox="0 0 64 44" fill="#fff"><path d="M2 10l12-6 8 16-10 6z"/><path d="M62 10l-12-6-8 16 10 6z"/><path d="M16 12l12-4 10 4 6 10-4 4-10-8-8 4z"/><path d="M14 26l8 8 4-2 4 4 4-2 4 4 6-4-10-12z"/></svg>
  </div>
  <h2 class="service-title">Interpreting</h2>
  <p class="service-text">Lorem ipsum dolor sit amet, consectetuer adipiscing elit, sed diam nonummy nibh.</p>
  <span class="btn">More</span>
</section>

<div class="abs video">
  <div class="video-frame" role="img" aria-label="Video still of a team of business professionals in suits"></div>
  <div class="video-bar">
    <svg width="10" height="12" viewBox="0 0 10 12"><path d="M0 0l10 6-10 6z" fill="#e53935"/></svg>
    <div class="progress"></div>
    <span>10:00</span>
  </div>
</div>
<section class="abs about">
  <h2 class="h-section">Who Are We?</h2>
  <p>We are a small, highly professional and qualified group of professionals with backgrounds in law, financial services and translation and interpretation that boasts experience in global consulting and auditing firms, law firms and companies from a cross section of industries. Sensitive to the workings of the financial world, we are detail-oriented experts striving to facilitate understanding among investors, companies and international organisations.</p>
  <span class="btn btn-dark">More</span>
</section>

<section class="abs why" role="img" aria-label="Dark background of modern glass architecture">
  <h2 class="h-section">Why Choose Us?</h2>
  <div class="reason" style="left:100px">
    <div class="reason-icon"><svg width="34" height="28" viewBox="0 0 34 28" fill="#fff"><ellipse cx="16" cy="15" rx="13" ry="10"/><rect x="7" y="22" width="5" height="6"/><rect x="19" y="22" width="5" height="6"/><path d="M28 12l6-2v6l-6-1z"/><rect x="13" y="3" width="7" height="3" rx="1"/></svg></div>
    <h3>Save Money</h3>
    <p>Lorem ipsum dolor sit amet, consec­tetuer adipiscing elit, sed diam non­ummy nibh euismod tincidunt ut laoreet dolore magna aliquam erat volutpat. Ut wisi enim ad minim veniam, quis nostrud exerci tation ullamcorper sudolore te feugait nulla facilisi. ..</p>
  </div>
  <div class="reason" style="left:432px">
    <div class="reason-icon"><svg width="30" height="30" viewBox="0 0 24 24" fill="#fff"><path d="M12 2l3 7 7 .6-5.3 4.6 1.6 7L12 17.5 5.7 21.2l1.6-7L2 9.6 9 9z"/></svg></div>
    <h3>Quality Guaranteed</h3>
    <p>Lorem ipsum dolor sit amet, consec­tetuer adipiscing elit, sed diam non­ummy nibh euismod tincidunt ut laoreet dolore magna aliquam erat volutpat. Ut wisi enim ad minim veniam, quis nostrud exerci tation ullamcorper sudolore te feugait nulla facilisi. ..</p>
  </div>
  <div class="reason" style="left:766px">
    <div class="reason-icon"><svg width="34" height="32" viewBox="0 0 34 32" fill="#fff"><circle cx="13" cy="12" r="6"/><path d="M2 32c0-8 5-12 11-12s11 4 11 12z"/><rect x="20" y="0" width="13" height="9" rx="2"/></svg></div>
    <h3>Native Translators Only</h3>
    <p>Lorem ipsum dolor sit amet, consec­tetuer adipiscing elit, sed diam non­ummy nibh euismod tincidunt ut laoreet dolore magna aliquam erat volutpat. Ut wisi enim ad minim veniam, quis nostrud exerci tation ullamcorper sudolore te feugait nulla facilisi. ..</p>
  </div>
</section>

<h2 class="abs h-section clients-h">Our Clients</h2>
<div class="abs clients">
  <div class="client"><span class="client-dot"></span>Northvale</div>
  <div class="client"><span class="client-dot"></span>Northvale</div>
  <div class="client"><span class="client-dot"></span>Northvale</div>
  <div class="client"><span class="client-dot"></span>Northvale</div>
  <div class="client"><span class="client-dot"></span>Northvale</div>
</div>

<footer class="abs footer">
  <div class="fcol" style="left:100px">
    <h4>Quick Links</h4>
    <ul><li>Home</li><li>About Us</li><li>FAQ's</li><li>Our Clients</li><li>Privacy Policy</li></ul>
  </div>
  <div class="fcol" style="left:350px">
    <h4>Services We Offer</h4>
    <ul><li>Legal Translation</li><li>Financial Translation</li><li>Document Translation</li><li>Interpreting</li><li>Service Levels</li></ul>
  </div>
  <div class="fcol contact" style="left:601px">
    <h4>Contact Info</h4>
    <p>Address: 118 Harbor Crest Lane<br>Brookvale, ST 40210</p>
    <p>Phone: (555) 014-2290</p>
    <p>Fax: (555) 014-2291</p>
    <p>Mail: <a>info@lumarin-example.com</a></p>
  </div>
  <div class="fcol" style="left:850px">
    <h4>Send Us a Message</h4>
    <div class="field">Name</div>
    <div class="field">Email</div>
    <div class="field field-msg">Message</div>
    <span class="send">Send Message</span>
  </div>
</footer>

</body>
</html>
```